Logistics Website Design

See website https://tqfreightglobal.com for theme and color details. Need the site to be re-done and reflect some of the designs shown in this list here: https://pixelvane.com/tags/logistics-company-website

Target Market(s)

Logistics & Transportation

Industry/Entity Type

Logistics and Supply Chain

Coding

Number of Pages Required

5+ page

Requirements
Must have
• Colors must match theme of logo. Looking for a sleek, interactive design.

```html
<!DOCTYPE html>
<html lang="en">
<head>
<meta charset="utf-8">
<title>TQ Freight Global</title>
<link rel="stylesheet" href="https://fonts.googleapis.com/css2?family=Oswald:wght@500;600;700&family=Rethink+Sans:wght@400;500;600&display=swap">
<style>
:root{
  --orange:#e8612f;
  --orange-light:#f07a45;
  --rust:#b3340f;
  --rust-dark:#8f2a0c;
  --peach:#fde5dc;
  --peach-soft:#fbe9e2;
  --ink:#1b1b1b;
  --body:#333;
  --white:#fff;
}
*{box-sizing:border-box;margin:0;padding:0}
html,body{width:1200px;height:3684px;overflow:hidden;background:var(--white)}
body{position:relative;font-family:"Rethink Sans",Arial,sans-serif;color:var(--body)}
.abs{position:absolute}
.display{font-family:"Oswald",Impact,sans-serif;font-weight:700;text-transform:uppercase;letter-spacing:-0.5px}
.accent{color:var(--rust)}

/* header */
.site-header{left:0;top:0;width:1200px;height:79px;background:var(--white);z-index:5}
.brand-disc{left:107px;top:0;width:94px;height:94px;border-radius:50%;background:var(--white);box-shadow:0 2px 6px rgba(0,0,0,.15);display:flex;align-items:center;justify-content:center;text-align:center}
.brand-name{font-family:"Oswald",sans-serif;font-weight:700;font-size:13px;line-height:1.1;color:var(--rust);text-transform:uppercase}
.nav a{position:absolute;top:28px;font-family:"Oswald",sans-serif;font-weight:600;font-size:17px;color:var(--ink);text-decoration:none;text-transform:uppercase}
.nav a.current{color:var(--orange)}
.btn{display:flex;align-items:center;justify-content:space-between;padding-left:24px;padding-right:5px;border-radius:4px;background:linear-gradient(180deg,var(--orange-light),var(--orange));color:var(--white);font-family:"Oswald",sans-serif;font-weight:600;font-size:16px;text-transform:uppercase;box-shadow:0 3px 6px rgba(179,52,15,.3)}
.btn .chev{width:30px;height:30px;border-radius:50%;background:var(--rust);display:flex;align-items:center;justify-content:center}

/* hero */
.hero{left:0;top:79px;width:1200px;height:585px;background:radial-gradient(ellipse at 70% 40%,#f3a15f 0%,#c45a25 35%,#6e2a12 75%,#3a170b 100%)}
.hero-title{left:112px;top:165px;font-size:88px;line-height:96px;color:var(--white)}
.hero-sub{left:112px;top:518px;font-family:"Oswald",sans-serif;font-weight:500;font-size:23px;line-height:27px;color:var(--white)}
.ring-btn{width:30px;height:30px;border:2px solid var(--orange-light);border-radius:50%;display:flex;align-items:center;justify-content:center}

/* services */
.section-title{font-size:48px;color:var(--ink)}
.lead{font-size:16px;line-height:25px;color:var(--body)}
.svc-card{width:309px;height:375px}
.svc-photo{position:absolute;left:0;top:0;width:309px;height:285px}
.svc-info{position:absolute;left:16px;top:215px;width:277px;height:160px;background:var(--peach);border-bottom:3px solid var(--orange);text-align:center;padding:20px 18px 0}
.svc-info h3{font-size:28px;color:var(--ink);margin-bottom:10px}
.svc-info p{font-size:12px;line-height:17px;color:var(--body)}
.arrow-dot{width:30px;height:30px;border-radius:50%;background:var(--rust);display:flex;align-items:center;justify-content:center}

/* about */
.portrait{left:143px;top:1271px;width:404px;height:404px;border-radius:50%;border:4px solid var(--orange-light);background:linear-gradient(180deg,#f4f4f4,#e2e6ee 60%,#2c4a86 85%)}
.name-plate{left:212px;top:1606px;width:267px;height:77px;background:linear-gradient(180deg,var(--orange-light),var(--orange));border:3px solid var(--rust);text-align:center;color:var(--white);padding-top:8px;box-shadow:0 4px 10px rgba(0,0,0,.2)}
.name-plate strong{display:block;font-family:"Oswald",sans-serif;font-weight:600;font-size:27px;line-height:32px;text-transform:uppercase}
.name-plate span{font-family:"Oswald",sans-serif;font-weight:500;font-size:16px;text-transform:uppercase}
.sub-title{font-family:"Oswald",sans-serif;font-weight:500;font-size:22px;color:var(--ink);text-transform:uppercase}
.story-photo{left:600px;top:1688px;width:600px;height:458px;background:linear-gradient(90deg,rgba(255,255,255,1) 0%,rgba(200,214,232,.6) 25%,#9fb4cf 55%,#7d8d9f 100%)}

/* industries */
.industries{left:0;top:2146px;width:1200px;height:497px;background:linear-gradient(180deg,var(--rust) 0%,#c24818 60%,#d86a3a 100%)}
.ind-card{top:2302px;width:222px;height:248px;background:var(--peach);border-bottom:6px solid var(--orange-light);text-align:center}
.ind-card svg{margin-top:52px}
.ind-card h3{position:absolute;left:0;right:0;top:188px;font-size:23px;color:var(--ink)}

/* contact */
.contact-panel{left:112px;top:2737px;width:976px;height:529px;border-radius:70px;background:var(--peach)}
.info-item{display:flex;align-items:center;gap:12px;font-size:14px;line-height:19px;color:var(--rust)}
.icon-badge{width:24px;height:24px;border-radius:50%;border:1px solid var(--orange);background:var(--white);display:flex;align-items:center;justify-content:center;flex:none}
.field{height:46px;background:var(--white);border-radius:3px;display:flex;align-items:center;gap:12px;padding-left:20px;font-size:14px;color:var(--ink);box-shadow:0 1px 3px rgba(0,0,0,.05)}
.field.tall{height:119px;align-items:flex-start;padding-top:16px}

/* footer */
.site-footer{left:0;top:3266px;width:1200px;height:418px;background:linear-gradient(180deg,#fff 0%,#fbeeea 60%,#f6ece9 100%)}
.foot-head{font-family:"Oswald",sans-serif;font-weight:600;font-size:24px;color:var(--rust);text-transform:uppercase;border-left:3px solid var(--rust);padding-left:12px;line-height:24px}
.foot-list{list-style:none;font-size:16px;line-height:26px;color:#555}
.social{width:24px;height:24px;border-radius:50%;border:1.5px solid var(--rust);background:var(--white)}
.foot-contact{display:flex;gap:14px;align-items:flex-start;font-size:16px;line-height:20px;color:var(--ink)}
.foot-contact .icon-badge{width:30px;height:30px}
</style>
</head>
<body>

<header class="abs site-header">
  <div class="abs brand-disc"><span class="brand-name">TQ Freight<br>Global</span></div>
  <nav class="nav">
    <a class="current" style="left:414px">Home</a>
    <a style="left:491px">Services</a>
    <a style="left:591px">Industries</a>
    <a style="left:707px">Request a Quote</a>
    <a style="left:863px">About Us</a>
  </nav>
  <div class="abs btn" style="left:955px;top:19px;width:133px;height:42px;padding-left:14px">Contact Us
    <span class="chev"><svg width="10" height="10" viewBox="0 0 10 10"><path d="M3 1l4 4-4 4" stroke="#fff" stroke-width="1.8" fill="none"/></svg></span></div>
</header>

<section>
  <div class="abs hero" role="img" aria-label="Semi truck with trailer driving on a highway at sunset, glowing orange light"></div>
  <div class="abs ring-btn" style="left:35px;top:335px"><svg width="10" height="10" viewBox="0 0 10 10"><path d="M1 7l4-4 4 4" stroke="#f07a45" stroke-width="1.8" fill="none"/></svg></div>
  <div class="abs ring-btn" style="left:35px;top:379px"><svg width="10" height="10" viewBox="0 0 10 10"><path d="M1 3l4 4 4-4" stroke="#f07a45" stroke-width="1.8" fill="none"/></svg></div>
  <h1 class="abs display hero-title">Delivering<br>Strength<br>in Every Mile</h1>
  <p class="abs hero-sub">Secure and reliable transportation<br>for all your cargo needs.</p>
  <div class="abs btn" style="left:112px;top:598px;width:153px;height:41px;padding-left:8px;font-size:15px;border:1px solid #fff">Request a Quote
    <span class="chev" style="background:transparent"><svg width="10" height="10" viewBox="0 0 10 10"><path d="M3 1l4 4-4 4" stroke="#fff" stroke-width="1.8" fill="none"/></svg></span></div>
</section>

<section>
  <h2 class="abs display section-title" style="left:112px;top:765px">Our <span class="accent">Services</span></h2>
  <p class="abs lead" style="left:114px;top:841px;width:290px">We provide a full range of transportation solutions designed to handle diverse freight requirements. Whether you're moving general goods or heavy equipment, our fleet and expertise ensure smooth and secure delivery across every mile.</p>
  <div class="abs btn" style="left:113px;top:1074px;width:155px;height:41px">Learn More
    <span class="chev"><svg width="10" height="10" viewBox="0 0 10 10"><path d="M3 1l4 4-4 4" stroke="#fff" stroke-width="1.8" fill="none"/></svg></span></div>

  <div class="abs arrow-dot" style="left:424px;top:879px"><svg width="10" height="10" viewBox="0 0 10 10"><path d="M7 1L3 5l4 4" stroke="#fff" stroke-width="1.8" fill="none"/></svg></div>
  <div class="abs arrow-dot" style="left:1138px;top:879px"><svg width="10" height="10" viewBox="0 0 10 10"><path d="M3 1l4 4-4 4" stroke="#fff" stroke-width="1.8" fill="none"/></svg></div>

  <article class="abs svc-card" style="left:473px;top:752px">
    <div class="svc-photo" role="img" aria-label="Flatbed truck loaded with steel beams inside a lit warehouse" style="background:linear-gradient(180deg,#6b3a1c,#c98a4e 45%,#4a3a30)"></div>
    <div class="svc-info"><h3 class="display">Flatbed</h3><p>Ideal for oversized and irregular loads, our flatbed services offer flexibility for transporting construction materials, machinery, and large equipment.</p></div>
  </article>
  <article class="abs svc-card" style="left:808px;top:752px">
    <div class="svc-photo" role="img" aria-label="Step deck trailer carrying equipment along a mossy forest road" style="background:linear-gradient(180deg,#5f6f3a,#a1a85a 45%,#8c8c88)"></div>
    <div class="svc-info"><h3 class="display">Step Deck</h3><p>Perfect for taller freight that exceeds standard height limits. Our step deck trailers provide extra vertical space, making them suitable for industrial equipment.</p></div>
  </article>
</section>

<section>
  <div class="abs portrait" role="img" aria-label="Portrait of the director of agency sales in a blue suit"></div>
  <div class="abs name-plate"><strong>Darren Okafor</strong><span>Director of Agency Sales</span></div>
  <h2 class="abs display section-title" style="left:635px;top:1257px">About <span class="accent">Us</span></h2>
  <h3 class="abs sub-title" style="left:636px;top:1344px">Leadership Team</h3>
  <p class="abs lead" style="left:636px;top:1382px;width:455px">TQ Freight Global™ was born out of real-world experience in the fitness equipment industry. What started as a company shipping strength equipment, cardio machines, and training gear to gyms, schools, and commercial facilities quickly evolved into something bigger. As order volume grew and supply chains became more complex, the team developed deep expertise in coordinating freight, managing</p>
  <div class="abs btn" style="left:635px;top:1589px;width:155px;height:41px">Learn More
    <span class="chev"><svg width="10" height="10" viewBox="0 0 10 10"><path d="M3 1l4 4-4 4" stroke="#fff" stroke-width="1.8" fill="none"/></svg></span></div>

  <div class="abs story-photo" role="img" aria-label="Silver semi truck on a highway with mountains behind"></div>
  <h3 class="abs sub-title" style="left:139px;top:1762px">Our Story</h3>
  <p class="abs lead" style="left:139px;top:1799px;width:455px">TQ Freight Global™ was born out of real-world experience in the fitness equipment industry. What started as a company shipping strength equipment, cardio machines, and training gear to gyms, schools, and commercial facilities quickly evolved into something bigger. As order volume grew and supply chains became more complex, the team developed deep expertise in coordinating freight, managing deliveries, and navigating the challenges of large-scale equipment transportation. That hands-on experience laid the foundation for what would eventually become a full-service logistics operation.</p>
</section>

<section>
  <div class="abs industries" role="img" aria-label="Faded truck on highway under a deep rust overlay"></div>
  <h2 class="abs display" style="left:0;width:1200px;top:2218px;text-align:center;font-size:48px;color:#fff">Our Industries</h2>
  <div class="abs ind-card" style="left:112px">
    <svg width="80" height="80" viewBox="0 0 80 80" fill="none" stroke="#111" stroke-width="3"><circle cx="42" cy="40" r="22"/><circle cx="42" cy="40" r="14"/><path d="M8 12v24M14 12v24M20 12v24M8 36h12M14 36v34"/><path d="M72 12c-8 6-8 20 0 26v32"/></svg>
    <h3 class="display">Food &amp; Beverage</h3>
  </div>
  <div class="abs ind-card" style="left:362px">
    <svg width="90" height="80" viewBox="0 0 90 80" fill="none" stroke="#111" stroke-width="3"><path d="M4 10h10l10 42h46l8-26"/><circle cx="30" cy="66" r="6"/><circle cx="64" cy="66" r="6"/><circle cx="52" cy="26" r="18"/><path d="M34 26h36M52 8c-8 10-8 26 0 36M52 8c8 10 8 26 0 36"/></svg>
    <h3 class="display">E-Commerce &amp; Retail</h3>
  </div>
  <div class="abs ind-card" style="left:613px">
    <svg width="96" height="80" viewBox="0 0 96 80" fill="none" stroke="#111" stroke-width="3"><circle cx="32" cy="26" r="10"/><path d="M32 6v8M32 38v8M12 26h8M44 26h8M18 12l6 6M40 34l6 6M18 40l6-6M40 18l6-6"/><rect x="56" y="38" width="12" height="12"/><rect x="70" y="30" width="12" height="20"/><rect x="6" y="56" width="86" height="16" rx="8"/><circle cx="20" cy="64" r="3"/><circle cx="36" cy="64" r="3"/><circle cx="52" cy="64" r="3"/><circle cx="68" cy="64" r="3"/></svg>
    <h3 class="display">Manufacturing</h3>
  </div>
  <div class="abs ind-card" style="left:865px">
    <svg width="90" height="80" viewBox="0 0 90 80" fill="none" stroke="#111" stroke-width="3"><path d="M45 40C30 28 22 20 28 10c5-7 13-5 17 2 4-7 12-9 17-2 6 10-2 18-17 30z"/><path d="M45 14v14M38 21h14"/><path d="M10 30v22l14 14v10M80 30v22L66 66v10"/><path d="M18 40l12 14M72 40L60 54"/></svg>
    <h3 class="display">Pharma &amp; Healthcare</h3>
  </div>
</section>

<section>
  <div class="abs contact-panel"></div>
  <h2 class="abs display section-title" style="left:0;width:1200px;top:2780px;text-align:center">Contact <span class="accent">Us</span></h2>
  <div class="abs info-item" style="left:286px;top:2862px">
    <span class="icon-badge"><svg width="12" height="12" viewBox="0 0 12 12"><path d="M6 11S2 7 2 4.5a4 4 0 018 0C10 7 6 11 6 11z" fill="#b3340f"/><circle cx="6" cy="4.5" r="1.4" fill="#fff"/></svg></span>482 Harbor Ridge Road<br>Fresno, CA 93721</div>
  <div class="abs info-item" style="left:509px;top:2862px">
    <span class="icon-badge"><svg width="12" height="12" viewBox="0 0 12 12"><path d="M2 2l2-.5 1.5 3-1 1a6 6 0 002.5 2.5l1-1 3 1.5L10.5 10C6 10 2 6 2 2z" fill="#b3340f"/></svg></span>+1 (555) 014 2290</div>
  <div class="abs info-item" style="left:721px;top:2866px">
    <span class="icon-badge" style="background:#fbd3c4"><svg width="12" height="12" viewBox="0 0 12 12"><rect x="1.5" y="3" width="9" height="6.5" rx="1" fill="#b3340f"/><path d="M1.5 3.5L6 7l4.5-3.5" stroke="#fff" fill="none"/></svg></span>info@tqfreightglobal.com</div>

  <div class="abs field" style="left:214px;top:2924px;width:379px"><svg width="14" height="14" viewBox="0 0 14 14" fill="none" stroke="#888"><circle cx="7" cy="5" r="3"/><path d="M1.5 13c1-3 3-4 5.5-4s4.5 1 5.5 4"/></svg>First Name*</div>
  <div class="abs field" style="left:608px;top:2924px;width:379px"><svg width="14" height="14" viewBox="0 0 14 14" fill="none" stroke="#888"><circle cx="7" cy="5" r="3"/><path d="M1.5 13c1-3 3-4 5.5-4s4.5 1 5.5 4"/></svg>Last Name*</div>
  <div class="abs field" style="left:214px;top:2989px;width:379px"><svg width="14" height="14" viewBox="0 0 14 14" fill="none" stroke="#888"><rect x="1" y="3" width="12" height="8" rx="1"/><path d="M1 3.5l6 4 6-4"/></svg>E-mail*</div>
  <div class="abs field" style="left:608px;top:2989px;width:379px"><svg width="14" height="14" viewBox="0 0 14 14" fill="none" stroke="#888"><path d="M2 2l2.5-.5 1.5 3-1 1a7 7 0 003.5 3.5l1-1 3 1.5L12 12C6.5 12 2 7.5 2 2z"/></svg>Phone Number*</div>
  <div class="abs field tall" style="left:214px;top:3050px;width:773px"><svg width="16" height="16" viewBox="0 0 16 16" fill="none" stroke="#888"><path d="M8 2a6 6 0 00-5 9.5L2 14l3-1a6 6 0 103-11z"/></svg>Leave Message</div>
  <div class="abs btn" style="left:523px;top:3205px;width:154px;height:41px;padding-left:38px">Submit
    <span class="chev"><svg width="10" height="10" viewBox="0 0 10 10"><path d="M3 1l4 4-4 4" stroke="#fff" stroke-width="1.8" fill="none"/></svg></span></div>
</section>

<footer class="abs site-footer">
  <div class="abs" style="left:176px;top:84px;width:118px;height:118px;border-radius:50%;border:3px solid var(--orange);background:#fff;display:flex;align-items:center;justify-content:center;text-align:center"><span class="brand-name" style="font-size:16px">TQ Freight<br>Global</span></div>
  <div class="abs social" style="left:188px;top:220px"></div>
  <div class="abs social" style="left:222px;top:220px"></div>
  <div class="abs social" style="left:256px;top:220px"></div>

  <h4 class="abs foot-head" style="left:410px;top:82px">Quick Links</h4>
  <ul class="abs foot-list" style="left:423px;top:126px"><li>Home</li><li>Services</li><li>Industries</li><li>Request a Quote</li><li>About Us</li><li>Contact Us</li></ul>
  <h4 class="abs foot-head" style="left:651px;top:82px">Support</h4>
  <ul class="abs foot-list" style="left:666px;top:126px"><li>Copyright</li><li>Legal</li><li>Privacy</li><li>Accessibility</li><li>Sitemap</li></ul>
  <h4 class="abs foot-head" style="left:859px;top:82px">Contact Us</h4>
  <div class="abs foot-contact" style="left:859px;top:124px">
    <span class="icon-badge"><svg width="14" height="14" viewBox="0 0 12 12"><path d="M2 2l2-.5 1.5 3-1 1a6 6 0 002.5 2.5l1-1 3 1.5L10.5 10C6 10 2 6 2 2z" fill="#b3340f"/></svg></span>
    <div>Phone Number<br><strong>(+1 555) 014 2290</strong></div></div>
  <div class="abs foot-contact" style="left:859px;top:196px">
    <span class="icon-badge"><svg width="14" height="14" viewBox="0 0 12 12"><path d="M6 11S2 7 2 4.5a4 4 0 018 0C10 7 6 11 6 11z" fill="#b3340f"/><circle cx="6" cy="4.5" r="1.4" fill="#fff"/></svg></span>
    <div>482 Harbor Ridge Road<br>Fresno, CA 93721</div></div>
  <div class="abs foot-contact" style="left:859px;top:268px">
    <span class="icon-badge"><svg width="14" height="14" viewBox="0 0 12 12"><rect x="1.5" y="3" width="9" height="6.5" rx="1" fill="#b3340f"/><path d="M1.5 3.5L6 7l4.5-3.5" stroke="#fff" fill="none"/></svg></span>
    <div style="padding-top:5px">hello@tqfreightglobal.com</div></div>

  <div class="abs" style="left:112px;top:319px;width:976px;height:1px;background:#e6b3a3"></div>
  <p class="abs" style="left:0;width:1200px;top:344px;text-align:center;font-size:15px;color:#555">© 2026. An independent agent of Halvorsen Carriers LLC.</p>
</footer>

</body>
</html>
```